New Business Card Design Project

Use the flyer uploaded and website www.harborlinebuilders.example for inspiration.
List Our Services on Backside of business cards
Marcus Delling
Harborline Builders Inc.
Licensed General Contractors
858-555-0147

Contact Information for Business Card

Use the flyer uploaded and website www.harborlinebuilders.example for inspiration. List Our Services on Backside of business cards Marcus Delling Harborline Builders Inc. Licensed General Contractors 858-555-0147

```html
<!DOCTYPE html>
<html lang="en">
<head>
<meta charset="utf-8">
<title>Harborline Builders — Business Card</title>
<link rel="stylesheet" href="https://fonts.googleapis.com/css2?family=Cormorant+Garamond:wght@500&family=Playfair+Display:wght@700&family=Arimo:wght@400&display=swap">
<style>
  :root {
    --page: #141415;
    --card: #2a2a2b;
    --card-edge: #353536;
    --ink: #f4f4f4;
    --ink-soft: #d9d9d9;
    --accent: #ffffff;
  }
  * { box-sizing: border-box; margin: 0; padding: 0; }
  html, body { width: 1200px; height: 963px; overflow: hidden; background: var(--page); }
  .canvas {
    width: 1200px; height: 963px;
    display: flex; flex-direction: column; align-items: center; justify-content: center; gap: 56px;
  }
  .card {
    position: relative;
    width: 700px; height: 400px;
    background: var(--card);
    border: 1px solid var(--card-edge);
    border-radius: 22px;
    overflow: hidden;
    color: var(--ink);
  }
  .brand-name {
    font-family: "Cormorant Garamond", serif;
    font-weight: 500;
    text-transform: uppercase;
    letter-spacing: 1px;
    color: var(--ink);
    white-space: nowrap;
  }
  /* front */
  .card--front .brand-name { position: absolute; left: 200px; top: 70px; font-size: 30px; }
  .contact { position: absolute; left: 56px; top: 196px; list-style: none; font-family: "Arimo", sans-serif; font-size: 18px; color: var(--ink-soft); }
  .contact li { display: flex; align-items: center; gap: 12px; margin-bottom: 10px; white-space: nowrap; }
  .contact svg { width: 16px; height: 16px; flex: none; }
  .holder { position: absolute; right: 64px; top: 168px; text-align: right; }
  .holder-name { font-family: "Playfair Display", serif; font-weight: 700; font-size: 28px; text-transform: uppercase; letter-spacing: 0.5px; white-space: nowrap; }
  .holder-title { font-family: "Arimo", sans-serif; font-size: 17px; color: var(--ink-soft); margin-top: 4px; white-space: nowrap; }
  .edge-tab { position: absolute; right: 0; top: 176px; width: 22px; height: 48px; background: var(--accent); }
  /* back */
  .services { position: absolute; left: 48px; top: 40px; }
  .services-heading { font-family: "Cormorant Garamond", serif; font-weight: 500; font-size: 32px; text-transform: uppercase; letter-spacing: 1px; margin-bottom: 10px; }
  .services-list { list-style: none; font-family: "Arimo", sans-serif; font-size: 15.5px; line-height: 1.62; }
  .services-list li { display: flex; align-items: center; gap: 8px; white-space: nowrap; }
  .services-list svg { width: 14px; height: 14px; flex: none; }
  .card--back .brand-name { position: absolute; right: 44px; top: 176px; font-size: 28px; }
</style>
</head>
<body>
<main class="canvas">
  <section class="card card--front" aria-label="Business card front">
    <div class="brand-name">Harborline Builders</div>
    <ul class="contact">
      <li>
        <svg viewBox="0 0 16 16" aria-hidden="true"><path d="M4 1.5 6 4.5 4.8 6c.8 1.9 2.4 3.5 4.2 4.3L10.5 9l3 2-1.2 2.6c-5.4-.3-9.6-4.5-9.9-9.9Z" fill="none" stroke="currentColor" stroke-width="1.4" stroke-linejoin="round"/></svg>
        <span>858-555-0147</span>
      </li>
      <li>
        <svg viewBox="0 0 16 16" aria-hidden="true"><g fill="none" stroke="currentColor" stroke-width="1.2"><circle cx="8" cy="8" r="6.5"/><ellipse cx="8" cy="8" rx="2.8" ry="6.5"/><path d="M1.5 8h13M2.5 4.8h11M2.5 11.2h11"/></g></svg>
        <span>www.harborlinebuilders.example</span>
      </li>
    </ul>
    <div class="holder">
      <div class="holder-name">Marcus Delling</div>
      <div class="holder-title">Licensed General Contractors</div>
    </div>
    <div class="edge-tab"></div>
  </section>

  <section class="card card--back" aria-label="Business card back">
    <div class="services">
      <h2 class="services-heading">Our Services</h2>
      <ul class="services-list">
        <li><svg viewBox="0 0 14 14" aria-hidden="true"><circle cx="7" cy="7" r="5.8" fill="none" stroke="currentColor" stroke-width="1.5"/><path d="M4.3 7.2 6.3 9 9.8 4.9" fill="none" stroke="currentColor" stroke-width="1.6"/></svg>Remodel: Kitchen &amp; Bath</li>
        <li><svg viewBox="0 0 14 14" aria-hidden="true"><circle cx="7" cy="7" r="5.8" fill="none" stroke="currentColor" stroke-width="1.5"/><path d="M4.3 7.2 6.3 9 9.8 4.9" fill="none" stroke="currentColor" stroke-width="1.6"/></svg>Painting: Interior &amp; Exterior</li>
        <li><svg viewBox="0 0 14 14" aria-hidden="true"><circle cx="7" cy="7" r="5.8" fill="none" stroke="currentColor" stroke-width="1.5"/><path d="M4.3 7.2 6.3 9 9.8 4.9" fill="none" stroke="currentColor" stroke-width="1.6"/></svg>Flooring: Carpet, Vinyl, Wood</li>
        <li><svg viewBox="0 0 14 14" aria-hidden="true"><circle cx="7" cy="7" r="5.8" fill="none" stroke="currentColor" stroke-width="1.5"/><path d="M4.3 7.2 6.3 9 9.8 4.9" fill="none" stroke="currentColor" stroke-width="1.6"/></svg>Window &amp; Door Replacement</li>
        <li><svg viewBox="0 0 14 14" aria-hidden="true"><circle cx="7" cy="7" r="5.8" fill="none" stroke="currentColor" stroke-width="1.5"/><path d="M4.3 7.2 6.3 9 9.8 4.9" fill="none" stroke="currentColor" stroke-width="1.6"/></svg>Plumbing: Repairs &amp; Upgrades</li>
        <li><svg viewBox="0 0 14 14" aria-hidden="true"><circle cx="7" cy="7" r="5.8" fill="none" stroke="currentColor" stroke-width="1.5"/><path d="M4.3 7.2 6.3 9 9.8 4.9" fill="none" stroke="currentColor" stroke-width="1.6"/></svg>Energy-Efficient Upgrades</li>
        <li><svg viewBox="0 0 14 14" aria-hidden="true"><circle cx="7" cy="7" r="5.8" fill="none" stroke="currentColor" stroke-width="1.5"/><path d="M4.3 7.2 6.3 9 9.8 4.9" fill="none" stroke="currentColor" stroke-width="1.6"/></svg>Deck &amp; Patio Construction</li>
        <li><svg viewBox="0 0 14 14" aria-hidden="true"><circle cx="7" cy="7" r="5.8" fill="none" stroke="currentColor" stroke-width="1.5"/><path d="M4.3 7.2 6.3 9 9.8 4.9" fill="none" stroke="currentColor" stroke-width="1.6"/></svg>Water &amp; Mold Damage</li>
        <li><svg viewBox="0 0 14 14" aria-hidden="true"><circle cx="7" cy="7" r="5.8" fill="none" stroke="currentColor" stroke-width="1.5"/><path d="M4.3 7.2 6.3 9 9.8 4.9" fill="none" stroke="currentColor" stroke-width="1.6"/></svg>Garage Renovation</li>
      </ul>
    </div>
    <div class="brand-name">Harborline Builders</div>
  </section>
</main>
</body>
</html>
```